Animal Horse & Bedding Company Needs a Website Coded & Designed

We need a website for a new animal bedding and feed company that is visually grabbing and vibrant. We would like to see a website that displays trust, quality and confidence. Needs to be responsive and mobile friendly for all browsers and coded for both Android & IOS. SEO is also important.

Joomla or Wordpress – must be both desktop and mobile friendly with fast page load speed. Need the ability to edit ourselves in Wordpress or Joomla.

Full details attached below with some layout and content ideas.

Coding

Coded - Design and coding required

Number of Pages Required

5+ page

Font styles to use
Sans Serif

Requirements
Must have
• Needs to be responsive and mobile friendly for all browsers and coded for both Android & IOS. SEO is also important.

Wordpress – must be both desktop and mobile friendly with fast page load speed. Need the ability to edit ourselves in Wordpress.

Logo Colours:
Dark Brown
CMYK: 50 / 70 / 80 / 70
Pantone: 4625C

Orange
CMYK: 0 / 50 / 100 / 0
Pantone: 144C
Nice to have
• Use picture of building attached and super impose logo on building.

```html
<!DOCTYPE html>
<html lang="en">
<head>
<meta charset="utf-8">
<title>Golden Furrow Bedding &amp; Feed</title>
<link href="https://fonts.googleapis.com/css2?family=Montserrat:wght@400;500;600;700&family=Open+Sans:wght@400;600&display=swap" rel="stylesheet">
<style>
:root{
  --orange:#f7941d;
  --orange-deep:#f08a0f;
  --brown:#3d1e0f;
  --brown-mid:#5a2d16;
  --cream:#fdf9f4;
  --ink:#2b1a10;
  --body:#4a4440;
  --white:#ffffff;
}
*{box-sizing:border-box;margin:0;padding:0}
html,body{width:1200px;height:4016px;overflow:hidden}
body{position:relative;background:var(--white);font-family:"Open Sans",Arial,sans-serif;color:var(--body)}
.abs{position:absolute}
.heading{font-family:"Montserrat",Arial,sans-serif}

/* hero */
.hero{left:0;top:0;width:1200px;height:700px}
.hero-photo{position:absolute;left:0;top:0;width:1200px;height:700px;
  background:linear-gradient(180deg,#eef1f4 0%,#e3e8ec 38%,#7f8f6a 46%,#4f6a3c 56%,#8a2a22 72%,#9d2f25 86%,#7b2a20 100%)}
.hero-edge{position:absolute;left:0;top:660px}
.site-header{position:absolute;left:0;top:0;width:1200px;height:95px}
.brand{position:absolute;display:flex;align-items:center;gap:10px;font-family:"Montserrat",Arial,sans-serif;font-weight:600;color:var(--brown);letter-spacing:1px}
.brand-dot{width:34px;height:34px;border-radius:50%;background:var(--orange)}
.header-brand{left:100px;top:28px;font-size:26px}
.main-nav{position:absolute;left:466px;top:38px;display:flex;gap:0;font-family:"Montserrat",Arial,sans-serif;font-size:12.5px;font-weight:500;color:var(--brown)}
.main-nav a{color:inherit;text-decoration:none;margin-right:48px}
.main-nav a.active{color:var(--brown);font-weight:600}
.btn{display:inline-flex;align-items:center;justify-content:center;gap:6px;border-radius:30px;font-family:"Montserrat",Arial,sans-serif;font-weight:700;text-decoration:none;font-size:12.5px}
.btn-orange{background:var(--orange);color:var(--white)}
.quote-btn{position:absolute;left:950px;top:28px;width:155px;height:40px}
.hero-title{position:absolute;left:0;top:138px;width:1200px;text-align:center;font-size:38px;font-weight:500;color:var(--ink);letter-spacing:.5px}
.hero-sub{position:absolute;left:0;top:186px;width:1200px;text-align:center;font-size:26px;font-weight:500;color:var(--orange);letter-spacing:12px}
.learn-btn{position:absolute;left:538px;top:234px;width:137px;height:40px;font-size:11.5px}

/* about */
.about-photo{left:106px;top:758px;width:405px;height:405px;border-radius:50%;background:radial-gradient(circle at 45% 40%,#9a5a2e 0%,#b78a5e 35%,#c9b08a 65%,#a9b2b8 100%)}
.about-photo-small{left:312px;top:970px;width:242px;height:242px;border-radius:50%;border:6px solid var(--white);background:linear-gradient(135deg,#d7dde2 0%,#8a6a4a 45%,#6b4a2c 100%)}
.section-title{font-family:"Montserrat",Arial,sans-serif;font-weight:600;color:var(--ink)}
.about-title{left:584px;top:802px;font-size:33px}
.about-title span{color:var(--orange)}
.title-rule{height:3px;background:var(--orange)}
.about-rule{left:584px;top:846px;width:60px}
.about-copy{left:586px;top:878px;width:505px;font-size:12.6px;line-height:21px}
.about-copy p{margin-bottom:19px}

/* feature cards */
.card{top:1287px;width:347px;height:268px;border-radius:0 60px 0 0;color:var(--white);text-align:center;padding-top:38px}
.card-a{left:86px;background:linear-gradient(135deg,#f79a24,#f58e14)}
.card-b{left:444px;background:linear-gradient(135deg,#4a2613,#3a1c0d)}
.card-c{left:802px;background:linear-gradient(135deg,#f8a02d,#f48c14)}
.card svg{display:block;margin:0 auto 8px}
.card-title{font-family:"Montserrat",Arial,sans-serif;font-size:20px;font-weight:500;line-height:23px;letter-spacing:.5px}
.card-text{font-size:11px;line-height:19px;margin:18px auto 0;width:240px}

/* bedding */
.bedding{left:0;top:1555px;width:1200px;height:890px;background:var(--cream)}
.bedding-title{left:0;top:1628px;width:1200px;text-align:center;font-size:33px}
.bedding-rule{left:580px;top:1672px;width:58px}
.bed-arc{left:380px;top:1700px}
.center-mark{left:480px;top:1790px;width:240px;text-align:center}
.center-mark .brand-dot{width:70px;height:70px;margin:0 auto 16px}
.center-mark span{display:block;font-family:"Montserrat",Arial,sans-serif;font-weight:600;font-size:26px;color:var(--brown);letter-spacing:1px}
.bed-icon{width:76px;height:76px;border-radius:50%;display:flex;align-items:center;justify-content:center}
.bed-icon.o{background:var(--orange)}
.bed-icon.d{background:var(--brown)}
.bed-label{font-size:14px;line-height:20px;color:var(--ink)}
.bed-label.r{text-align:right}
.bed-label.c{text-align:center}
.outline-dark{background:var(--brown);color:var(--white)}
.bedding-btn{left:508px;top:2320px;width:188px;height:52px;font-size:14px}

/* feed */
.feed{left:0;top:2440px;width:1200px;height:640px;background:linear-gradient(180deg,#f99a24 0%,#f7931a 100%)}
.feed-edge{left:0;top:2425px}
.feed-title{left:0;top:2484px;width:1200px;text-align:center;font-size:33px;color:var(--white);font-weight:500}
.feed-copy{left:200px;top:2543px;width:830px;text-align:center;color:#fff3e0;font-size:12.6px;line-height:21px}
.feed-item{display:flex;align-items:center;gap:10px;color:var(--white);font-family:"Montserrat",Arial,sans-serif;font-weight:600;font-size:13.5px;line-height:16px}
.feed-bowls{left:745px;top:2625px;width:400px;height:385px;border-radius:48% 52% 46% 54%;background:radial-gradient(circle at 55% 40%,#8d7a46 0%,#5a4a2a 40%,#2a2622 75%,#1e1c1b 100%);transform:rotate(-12deg)}
.feed-btn{left:519px;top:2976px;width:160px;height:45px;border:2px solid var(--white);color:var(--white);background:transparent;font-size:14px}

/* delivery */
.map{left:132px;top:3147px;width:446px;height:422px;border-radius:40px 120px 60px 140px;background:linear-gradient(180deg,#5b2c13 0%,#5b2c13 42%,#f39416 42%,#f0a024 100%)}
.delivery-title{left:662px;top:3196px;font-size:32px;line-height:40px;font-weight:500}
.delivery-title span{color:var(--orange)}
.delivery-copy{left:668px;top:3312px;width:430px;font-size:12.6px;line-height:22px}
.delivery-copy p{margin-bottom:4px}
.contact-btn{left:664px;top:3422px;width:146px;height:45px;border:2px solid var(--brown-mid);color:var(--orange);background:transparent;font-size:13px}

/* footer */
.footer{left:0;top:3600px;width:1200px;height:416px;background:var(--brown)}
.footer-edge{left:0;top:3585px}
.footer-brand{left:120px;top:3725px;flex-direction:column;gap:14px;color:var(--white);font-size:30px;text-align:center}
.footer-brand .brand-dot{width:44px;height:44px}
.socials{left:168px;top:3814px;display:flex;gap:7px}
.socials span{width:32px;height:32px;border-radius:50%;background:var(--orange)}
.foot-head{font-family:"Montserrat",Arial,sans-serif;color:var(--white);font-size:15px;font-weight:500;letter-spacing:.5px}
.foot-list{list-style:none;color:#f1e6dc;font-size:12px;line-height:26px}
.foot-contact{color:#f1e6dc;font-size:11px}
.foot-contact div{display:flex;gap:10px;align-items:flex-start;line-height:25px}
.email-field{left:865px;top:3722px;width:230px;height:36px;border:1px solid #9b7b66;border-radius:20px;color:#d9c8bb;font-size:10.5px;padding:10px 20px}
.subscribe{left:870px;top:3772px;width:132px;height:34px;font-size:11px}
.copyright{left:0;top:3964px;width:1200px;text-align:center;color:#c9b6a8;font-size:10.5px}
</style>
</head>
<body>

<section class="abs hero">
  <div class="hero-photo" role="img" aria-label="Aerial photo of red barns and paddocks of the bedding and feed farm under a pale sky"></div>
  <svg class="hero-edge" width="1200" height="45" viewBox="0 0 1200 45" aria-hidden="true"><polygon fill="#ffffff" points="0,22 40,18 75,25 120,15 170,24 230,16 290,26 340,17 400,23 460,14 520,25 580,18 640,26 700,15 760,24 820,17 880,25 940,16 1000,24 1060,18 1120,26 1160,17 1200,22 1200,45 0,45"/></svg>
  <header class="site-header">
    <div class="brand header-brand"><span class="brand-dot"></span>GOLDEN FURROW</div>
    <nav class="main-nav">
      <a class="active">HOME</a><a>ABOUT</a><a>FEED</a><a>BEDDING</a><a>CONTACT US</a>
    </nav>
    <a class="btn btn-orange quote-btn">REQUEST QUOTE ›</a>
  </header>
  <h1 class="heading hero-title">WELCOME TO GOLDEN FURROW</h1>
  <div class="heading hero-sub">BEDDING &amp; FEED</div>
  <a class="btn btn-orange learn-btn">LEARN MORE ›</a>
</section>

<div class="abs about-photo" role="img" aria-label="Chestnut horse resting on straw bedding"></div>
<div class="abs about-photo-small" role="img" aria-label="Horse eating feed from a bucket held over a fence"></div>
<h2 class="abs section-title about-title"><span>ABOUT</span> GOLDEN FURROW</h2>
<div class="abs title-rule about-rule"></div>
<div class="abs about-copy">
  <p>Looking for the best bedding and feed for your horse, livestock or household pet look no further. We use premium locally sourced straw and hay in all of our products and are committed in providing quality products and service.</p>
  <p>Your animal deserves the very best in health and comfort to keep them healthy, strong and happy. Our products are designed for horses, livestock (goats, cattle and sheep), small caged animals (rabbits, guinea pigs and more).</p>
  <p>Golden Furrow offers supply and delivery of fresh bedding as well as removal of waste bedding. Let us deliver you a container of fresh straw and haul your waste bedding away. A full service solution that is sustainable and responsible.</p>
</div>

<div class="abs bedding"></div>

<article class="abs card card-a">
  <svg width="46" height="62" viewBox="0 0 46 62" fill="none" stroke="#fff" stroke-width="2.2"><circle cx="23" cy="22" r="18"/><circle cx="23" cy="22" r="11"/><path d="M12 36 8 58l8-5 5 7 2-22M34 36l4 22-8-5-5 7-2-22"/></svg>
  <div class="card-title">QUALITY<br>GUARANTEED</div>
  <p class="card-text">Grown for quality - 100% natural with no chemicals or additives</p>
</article>
<article class="abs card card-b">
  <svg width="54" height="58" viewBox="0 0 54 58" fill="none" stroke="#fff" stroke-width="2.4"><path d="M10 8C2 24 6 46 27 52 48 46 52 24 44 8"/><path d="M18 16l18 18M36 16 18 34"/></svg>
  <div class="card-title">FULL SERVICE<br>SOLUTION</div>
  <p class="card-text">Dedicated in providing a full service solution of bedding supply &amp; waste removal</p>
</article>
<article class="abs card card-c">
  <svg width="60" height="60" viewBox="0 0 60 60" fill="none" stroke="#fff" stroke-width="2.2"><ellipse cx="30" cy="38" rx="22" ry="16"/><path d="M16 50v6M42 50v6M52 36h5"/><circle cx="30" cy="10" r="6"/></svg>
  <div class="card-title">CONVENIENT &amp; COST<br>EFFECTIVE</div>
  <p class="card-text">Compressed bags , pellets or bulk products saving in shipping costs</p>
</article>

<h2 class="abs section-title bedding-title">BEDDING</h2>
<div class="abs title-rule bedding-rule"></div>

<svg class="abs bed-arc" width="440" height="440" viewBox="0 0 440 440" aria-hidden="true">
  <path d="M76 66 A210 210 0 1 0 344 66" fill="none" stroke="#8a7a6f" stroke-width="1.2"/>
  <g fill="#f7941d">
    <circle cx="76" cy="66" r="6"/><circle cx="11" cy="235" r="6"/><circle cx="71" cy="385" r="6"/>
    <circle cx="220" cy="427" r="6"/><circle cx="362" cy="383" r="6"/><circle cx="424" cy="233" r="6"/><circle cx="344" cy="56" r="6"/>
  </g>
</svg>
<div class="abs center-mark"><div class="brand-dot"></div><span>GOLDEN FURROW</span></div>

<div class="abs bed-icon o" style="left:356px;top:1725px"><svg width="34" height="40" viewBox="0 0 34 40" fill="none" stroke="#fff" stroke-width="2"><path d="M17 2C4 14 4 28 17 36 30 28 30 14 17 2ZM17 8v32M17 20l-6-6M17 26l7-7"/></svg></div>
<div class="abs bed-label r" style="left:190px;top:1741px;width:150px">100% Natural<br>Chopped Straw</div>

<div class="abs bed-icon d" style="left:302px;top:1898px"><svg width="42" height="42" viewBox="0 0 42 42" fill="none" stroke="#fff" stroke-width="2"><circle cx="21" cy="21" r="17"/><path d="M9 9l24 24"/></svg></div>
<div class="abs bed-label r" style="left:180px;top:1925px;width:106px">Low Dust</div>

<div class="abs bed-icon o" style="left:365px;top:2065px"><svg width="40" height="40" viewBox="0 0 40 40" fill="none" stroke="#fff" stroke-width="2"><circle cx="20" cy="20" r="17"/><path d="M15 8h10M17 8v10l-7 12h20l-7-12V8M6 34 34 6"/></svg></div>
<div class="abs bed-label r" style="left:200px;top:2083px;width:152px">Chemical &amp;<br>Additive Free</div>

<div class="abs bed-icon d" style="left:562px;top:2146px"><svg width="42" height="42" viewBox="0 0 42 42" fill="none" stroke="#fff" stroke-width="1.8"><circle cx="13" cy="26" r="7"/><circle cx="26" cy="30" r="5"/><circle cx="28" cy="16" r="6"/><circle cx="12" cy="11" r="3"/><path d="M34 6v6M31 9h6"/></svg></div>
<div class="abs bed-label c" style="left:520px;top:2230px;width:160px">Clean &amp; Highly<br>Absorbent</div>

<div class="abs bed-icon o" style="left:752px;top:2064px"><svg width="42" height="30" viewBox="0 0 42 30" fill="#fff"><path d="M2 26h38v3H2zM6 24l6-12h8l4 6h10l4 6z"/></svg></div>
<div class="abs bed-label" style="left:838px;top:2083px;width:150px">Cheaper than<br>Wood Shavings</div>

<div class="abs bed-icon d" style="left:817px;top:1897px"><svg width="42" height="42" viewBox="0 0 42 42" fill="none" stroke="#fff" stroke-width="2"><circle cx="21" cy="21" r="17"/><path d="M4 21h34M21 4c-8 9-8 25 0 34M21 4c8 9 8 25 0 34"/></svg></div>
<div class="abs bed-label" style="left:905px;top:1917px;width:170px">Economic – less used<br>and less wasted</div>

<div class="abs bed-icon o" style="left:759px;top:1724px"><svg width="44" height="40" viewBox="0 0 44 40" fill="none" stroke="#fff" stroke-width="2"><path d="M22 4 12 20h20zM6 36l8-14 8 14zM22 36l8-14 8 14z"/></svg></div>
<div class="abs bed-label" style="left:851px;top:1741px;width:200px">Environmentally Friendly –<br>Recyclable &amp; Compostable</div>

<a class="abs btn outline-dark bedding-btn">VIEW BEDDING ›</a>

<section class="abs feed" role="img" aria-label="Orange panel over a faint photo of straw bales in a barn"></section>
<svg class="abs feed-edge" width="1200" height="30" viewBox="0 0 1200 30" aria-hidden="true"><polygon fill="#f99a24" points="0,14 50,8 100,16 160,6 220,15 280,9 340,17 400,7 460,14 520,8 590,16 650,6 720,15 780,9 850,17 910,7 980,15 1040,8 1100,16 1160,9 1200,13 1200,30 0,30"/></svg>
<h2 class="abs section-title feed-title">OUR FEED</h2>
<p class="abs feed-copy">Hay cubes and pellets are made from premium hay offering a variety of animals a feed that is non-GMO and packed with natural nutrients. These pellets and cubes are less bulky to handle, store and ship. As well, they reduce the amount of wasted feed.</p>

<div class="abs feed-item" style="left:124px;top:2652px"><svg width="30" height="40" viewBox="0 0 30 40" fill="none" stroke="#fff" stroke-width="1.8"><path d="M15 2C3 14 3 28 15 36 27 28 27 14 15 2ZM15 8v32"/></svg>100% Natural</div>
<div class="abs feed-item" style="left:354px;top:2650px"><svg width="44" height="44" viewBox="0 0 40 40" fill="none" stroke="#fff" stroke-width="1.8"><circle cx="20" cy="20" r="17"/><path d="M15 8h10M17 8v10l-7 12h20l-7-12V8M6 34 34 6"/></svg>Chemical &amp;<br>Additive Free</div>
<div class="abs feed-item" style="left:556px;top:2654px"><svg width="52" height="44" viewBox="0 0 52 44" fill="none" stroke="#fff" stroke-width="1.8"><path d="M26 4l12 6-12 6-12-6zM14 10v12l12 6 12-6V10M4 26l10-5 12 6v12l-12 5-10-5zM26 27l12-6 10 5v12l-10 5-12-6"/></svg>Available in<br>Pellets or Cubes</div>

<div class="abs feed-item" style="left:114px;top:2750px"><svg width="46" height="44" viewBox="0 0 46 44" fill="none" stroke="#fff" stroke-width="1.8"><circle cx="14" cy="28" r="9"/><circle cx="30" cy="32" r="6"/><circle cx="28" cy="14" r="7"/><circle cx="8" cy="10" r="3"/><path d="M40 4v6M37 7h6"/></svg>Clean - Eliminates<br>Dust From Feeding<br>Baled Hay</div>
<div class="abs feed-item" style="left:354px;top:2752px"><svg width="40" height="48" viewBox="0 0 40 48" fill="none" stroke="#fff" stroke-width="1.8"><path d="M4 8h32M14 8V3h12v5M7 8l3 37h20l3-37M15 14v26M20 14v26M25 14v26"/></svg>Eliminate Waste<br>in Feeding</div>
<div class="abs feed-item" style="left:562px;top:2756px"><svg width="46" height="34" viewBox="0 0 46 34" fill="none" stroke="#fff" stroke-width="1.8"><path d="M3 20c6-12 12-12 16-4s10 8 14 0 8-8 10-2M3 28c6-12 12-12 16-4s10 8 14 0"/></svg>High Protein<br>Content</div>

<div class="abs feed-item" style="left:112px;top:2846px"><svg width="52" height="46" viewBox="0 0 52 46" fill="none" stroke="#fff" stroke-width="1.8"><circle cx="20" cy="20" r="17"/><path d="M24 12c-2-2-10-2-10 3s10 3 10 9-8 5-10 3M19 8v26"/><circle cx="40" cy="36" r="6"/><circle cx="40" cy="36" r="2"/></svg>Cost Effective</div>
<div class="abs feed-item" style="left:350px;top:2846px"><svg width="50" height="50" viewBox="0 0 50 50" fill="none" stroke="#fff" stroke-width="1.8"><path d="M40 14A20 20 0 1 1 30 6"/><path d="M14 24l8 9L46 4"/></svg>Convenient</div>
<div class="abs feed-item" style="left:564px;top:2850px"><svg width="46" height="42" viewBox="0 0 44 40" fill="none" stroke="#fff" stroke-width="1.8"><path d="M22 4 12 20h20zM6 36l8-14 8 14zM22 36l8-14 8 14z"/></svg>Less wasted<br>feed</div>

<div class="abs feed-bowls" role="img" aria-label="Two dark scoops filled with mixed feed pellets and grain"></div>
<a class="abs btn feed-btn">VIEW FEED ›</a>

<div class="abs map" role="img" aria-label="Map of Canada in brown and the United States in orange showing delivery area"></div>
<h2 class="abs section-title delivery-title"><span>DELIVERY IN</span><br>CANADA &amp; USA</h2>
<div class="abs delivery-copy">
  <p>Looking for the best bedding and feed for your horse, livestock or household pet look no further.</p>
  <p>We use premium locally sourced straw and hay in all of our products and are committed in providing quality products and service.</p>
</div>
<a class="abs btn contact-btn">CONTACT US</a>

<footer class="abs footer"></footer>
<svg class="abs footer-edge" width="1200" height="30" viewBox="0 0 1200 30" aria-hidden="true"><polygon fill="#3d1e0f" points="0,14 40,9 90,17 150,7 210,15 270,8 330,16 390,6 460,15 520,9 580,17 640,7 700,14 770,8 830,16 890,6 960,15 1020,9 1080,17 1140,8 1200,13 1200,30 0,30"/></svg>
<div class="abs brand footer-brand"><span class="brand-dot"></span>GOLDEN FURROW</div>
<div class="abs socials" aria-label="Social links"><span></span><span></span><span></span><span></span></div>

<div class="abs foot-head" style="left:427px;top:3686px">SITEMAP</div>
<ul class="abs foot-list" style="left:427px;top:3718px">
  <li>Home</li><li>About Us</li><li>Our Bedding</li><li>Feed</li><li>Contact Us</li>
</ul>

<div class="abs foot-head" style="left:601px;top:3688px">CONTACT US</div>
<div class="abs foot-contact" style="left:604px;top:3718px;width:220px">
  <div><svg width="14" height="18" viewBox="0 0 14 18"><path d="M7 0a7 7 0 0 0-7 7c0 5 7 11 7 11s7-6 7-11a7 7 0 0 0-7-7Z" fill="#f7941d"/><circle cx="7" cy="7" r="2.5" fill="#3d1e0f"/></svg><span>48 Meadow Road, Fieldton<br>10101, United States</span></div>
  <div><svg width="14" height="14" viewBox="0 0 14 14"><path d="M3 1l3 3-2 2c1 2 2 3 4 4l2-2 3 3-2 2C6 13 1 8 1 3z" fill="#f7941d"/></svg><span>(555) 010-2468</span></div>
  <div style="margin-top:10px"><svg width="16" height="12" viewBox="0 0 16 12"><rect width="16" height="12" rx="1" fill="#f7941d"/><path d="M1 1l7 6 7-6" fill="none" stroke="#3d1e0f" stroke-width="1.2"/></svg><span>hello@goldenfurrow.com</span></div>
</div>

<div class="abs foot-head" style="left:865px;top:3686px">NEWSLETTER SIGN UP</div>
<div class="abs email-field">Email address</div>
<a class="abs btn btn-orange subscribe">SUBSCRIBE</a>

<p class="abs copyright">© Copyright 2020 . Golden Furrow . All Right Reserved</p>

</body>
</html>
```